Business Card Design Project

Business Card
We are rebranding with a new logo
Industry/Entity Type
Business
Contact Information for Business Card
Dennis Morvale +61 487215963 dennis@quorv.com.au P.O. Box 872 Fernlow QLD 4309
Requirements
Must have
- Logo

```html
<!DOCTYPE html>
<html lang="en">
<head>
<meta charset="utf-8">
<title>Quorv International – Business Card</title>
<link href="https://fonts.googleapis.com/css2?family=Open+Sans:wght@400;600;700&display=swap" rel="stylesheet">
<style>
  :root {
    --backdrop: #d8d4cf;
    --card-light: #ecebea;
    --card-light-shade: #dcdad8;
    --blue-deep: #0c3f66;
    --blue-mid: #17629a;
    --blue-bright: #1f78b8;
    --orange: #d9501e;
    --orange-dark: #b8321a;
    --red-band: #9c2a1c;
    --brand-blue: #1b5d9c;
    --text-light: #eef2f6;
    --text-name: #c9d2dc;
  }
  * { margin: 0; padding: 0; box-sizing: border-box; }
  html, body {
    width: 1200px; height: 969px; overflow: hidden;
    background: var(--backdrop);
    font-family: "Open Sans", Arial, sans-serif;
  }
  .card {
    position: absolute; left: 100px; top: 200px;
    width: 1000px; height: 570px;
    overflow: hidden;
    box-shadow: 0 12px 40px rgba(0,0,0,0.22);
  }
  .card-art { position: absolute; inset: 0; width: 100%; height: 100%; }
  .brand {
    position: absolute; left: 120px; top: 100px;
    color: var(--brand-blue); font-weight: 700;
  }
  .brand-name { font-size: 124px; line-height: 1; letter-spacing: -2px; }
  .brand-sub { font-size: 29px; letter-spacing: 4px; margin-top: 22px; }
  .contact {
    position: absolute; right: 58px; top: 305px;
    text-align: right; color: var(--text-light);
  }
  .contact-name {
    font-size: 30px; font-weight: 700; color: var(--text-name);
    letter-spacing: 0.5px; margin-bottom: 18px;
  }
  .contact-address { font-size: 22px; line-height: 33px; margin-bottom: 6px; margin-right: 38px; }
  .contact-line {
    display: flex; justify-content: flex-end; align-items: center;
    font-size: 22px; line-height: 34px;
  }
  .contact-line svg { width: 20px; height: 20px; margin-left: 18px; fill: var(--text-light); }
</style>
</head>
<body>
  <div class="card">
    <svg class="card-art" viewBox="0 0 1000 570" preserveAspectRatio="none">
      <defs>
        <linearGradient id="lightFace" x1="0" y1="0" x2="1" y2="1">
          <stop offset="0" stop-color="var(--card-light)"/>
          <stop offset="1" stop-color="var(--card-light-shade)"/>
        </linearGradient>
        <linearGradient id="blueFace" x1="0" y1="0" x2="1" y2="1">
          <stop offset="0" stop-color="var(--blue-bright)"/>
          <stop offset="0.5" stop-color="var(--blue-mid)"/>
          <stop offset="1" stop-color="var(--blue-deep)"/>
        </linearGradient>
      </defs>
      <rect width="1000" height="570" fill="url(#lightFace)"/>
      <path d="M170 0 C640 30 790 280 385 570 L1000 570 L1000 0 Z" fill="var(--orange)"/>
      <path d="M230 0 C680 40 800 300 405 570 L1000 570 L1000 0 Z" fill="var(--orange-dark)"/>
      <path d="M270 0 C700 50 790 320 420 570 L1000 570 L1000 0 Z" fill="var(--red-band)"/>
      <path d="M300 0 C710 60 770 330 430 570 L1000 570 L1000 0 Z" fill="url(#blueFace)"/>
    </svg>

    <div class="brand">
      <div class="brand-name">Quorv</div>
      <div class="brand-sub">INTERNATIONAL</div>
    </div>

    <div class="contact">
      <div class="contact-name">DENNIS MORVALE</div>
      <div class="contact-address">P.O. Box 872<br>Fernlow QLD 4309</div>
      <div class="contact-line">+61 487215963
        <svg viewBox="0 0 24 24"><path d="M4 9c0-3 4-5 8-5s8 2 8 5l-3 1-1-2c-2-1-6-1-8 0l-1 2zM6 12h12l2 8H4z"/></svg>
      </div>
      <div class="contact-line">dennis@quorv.com.au
        <svg viewBox="0 0 24 24"><path d="M3 6h18v12H3z M3 6l9 7 9-7" stroke="#17629a" stroke-width="1.5"/></svg>
      </div>
      <div class="contact-line">www.quorv.com.au
        <svg viewBox="0 0 24 24"><circle cx="12" cy="12" r="9"/><path d="M3 12h18M12 3c-4 4-4 14 0 18M12 3c4 4 4 14 0 18" stroke="#17629a" stroke-width="1.4" fill="none"/></svg>
      </div>
    </div>
  </div>
</body>
</html>
```